high end kitchens , needing new logo and business card design .

im looking a very simple looking design but classy that will stand out , i would like the design to be in the colours black , silver , gold and grey , although all colours dont need to be used in design , back of card to have name on it derek fawcett , address and phone number and website address , maybe fb logo . adrress is 42 mill row , holmbridge , bt19 4qa , 07912488265 , front of the card im open to design , back of card very simple i will want it matt black with silver writing , writing doesnt need to be that big

Target Market(s)

people with kitchen projects .

Industry/Entity Type

Interior Design

Contact Information for Business Card

front of business card th on it with maybe tallow hearths under it wrote smaller , maybe the card to be mate black with the writing in a gloss black or silver

Logo Text

th . tallow hearths

Font styles to use
Sans Serif
Script

Colors
1b1b1b
919191
f6f6f6
848484
ffc214
ec1f27

Requirements
Must have
• clean and simple , not too fussy ,
Nice to have
• n/a
Should not have
• n/a

```html
<!DOCTYPE html>
<html lang="en">
<head>
<meta charset="utf-8">
<title>Tallow Hearths — Business Card</title>
<link rel="stylesheet" href="https://fonts.googleapis.com/css2?family=Jost:wght@400;500&display=swap">
<style>
  :root {
    --backdrop: #2f2f2f;
    --card-matt: #2a2a2a;
    --gloss-black: #141414;
    --silver: #e4e4e4;
    --card-shadow: rgba(0, 0, 0, 0.45);
  }
  * { margin: 0; padding: 0; box-sizing: border-box; }
  html, body {
    width: 1200px;
    height: 780px;
    overflow: hidden;
    background: var(--backdrop);
    font-family: "Jost", "Futura", sans-serif;
  }
  .canvas {
    position: relative;
    width: 1200px;
    height: 780px;
  }
  .card {
    position: absolute;
    top: 196px;
    width: 254px;
    height: 390px;
    background: var(--card-matt);
    box-shadow: 0 6px 18px var(--card-shadow);
    text-align: center;
  }
  .card--contact { left: 314px; }
  .card--brand { left: 640px; }

  .brand-dot {
    position: absolute;
    left: 50%;
    border-radius: 50%;
    background: var(--gloss-black);
    transform: translateX(-50%);
  }
  .card--contact .brand-dot { top: 36px; width: 34px; height: 34px; }
  .card--brand .brand-dot { top: 150px; width: 46px; height: 46px; }

  .brand-name {
    position: absolute;
    left: 0;
    right: 0;
    color: var(--gloss-black);
    font-weight: 400;
    text-transform: uppercase;
    letter-spacing: 0.02em;
    white-space: nowrap;
  }
  .card--contact .brand-name { top: 88px; font-size: 25px; }
  .card--brand .brand-name { top: 212px; font-size: 25px; }

  .contact {
    position: absolute;
    left: 0;
    right: 0;
    top: 187px;
    color: var(--silver);
    font-weight: 400;
  }
  .contact__name {
    font-size: 19px;
    line-height: 28px;
    letter-spacing: 0.05em;
    text-transform: uppercase;
    margin-bottom: 19px;
  }
  .contact__line {
    font-size: 16.5px;
    line-height: 21.6px;
    letter-spacing: 0.03em;
    white-space: nowrap;
  }
  .contact__address { margin-top: 18px; }
  .contact__address .contact__line { line-height: 18px; }
</style>
</head>
<body>
<main class="canvas">
  <section class="card card--contact">
    <span class="brand-dot"></span>
    <p class="brand-name">Tallow Hearths</p>
    <div class="contact">
      <p class="contact__name">Derek Fawcett</p>
      <p class="contact__line">07912488265</p>
      <p class="contact__line">info@tallowhearths.com</p>
      <p class="contact__line">www.tallowhearths.com</p>
      <div class="contact__address">
        <p class="contact__line">42 mill row ,</p>
        <p class="contact__line">holmbridge , bt19 4qa</p>
      </div>
    </div>
  </section>

  <section class="card card--brand">
    <span class="brand-dot"></span>
    <p class="brand-name">Tallow Hearths</p>
  </section>
</main>
</body>
</html>
```